Graphic Design Zephyrmart Book Description

There is a book on Zephyrmart that is my competitor that has a large graphic design as part of the description for the book and I want a similar thing for my book to make it stand out more.

My competitors book is here: https://www.zephyrmart.example/Stellar-Chemistry-Novices-Grasping-Walkthrough/dp/K47RTPW612/

My book is here: https://www.zephyrmart.example/Stellar-Chemistry-Groundwork-Reactions-Bonding/dp/K9HXCVT27S/

You can see the kind of thing I am looking for on the book listing but I have attached an image below.

Thanks

Trevor

```html
<!DOCTYPE html>
<html lang="en">
<head>
<meta charset="utf-8">
<title>Quantum Physics – Book Description Graphic</title>
<link rel="stylesheet" href="https://fonts.googleapis.com/css2?family=Bebas+Neue&family=Poppins:wght@400;500;600;700;800&display=swap">
<style>
:root{
  --stage:#ececec;
  --yellow:#e4e41e;
  --yellow-bright:#f6f21a;
  --ink:#1d1d1d;
  --navy:#14205a;
  --navy-deep:#0b1642;
  --space:#0d2a7a;
  --gold:#f2c417;
  --gold-deep:#c99a0c;
  --white:#ffffff;
  --rule:#dcdcdc;
}
*{margin:0;padding:0;box-sizing:border-box}
html,body{width:1200px;height:1200px;overflow:hidden;background:var(--stage)}
.poster{position:absolute;left:220px;top:0;width:760px;height:1200px;background:var(--white);overflow:hidden;font-family:"Poppins",sans-serif;color:var(--ink)}
.hero-top{position:absolute;left:0;top:0;width:760px;height:240px;background:radial-gradient(circle at 75% 10%,var(--yellow-bright),var(--yellow) 60%,#d2d11a)}
.headline{position:absolute;left:0;width:760px;text-align:center;font-weight:400}
.headline-main{top:40px;font-family:"Bebas Neue",sans-serif;font-size:86px;line-height:80px}
.headline-sub{top:114px;font-family:"Bebas Neue",sans-serif;font-size:42px;line-height:40px;display:flex;justify-content:center;align-items:center;gap:10px}
.headline-sub::before,.headline-sub::after{content:"";width:78px;height:2px;background:var(--ink)}
.headline-topic{top:156px;font-weight:800;font-size:32px;line-height:34px}
.space-band{position:absolute;left:0;top:222px;width:760px;height:218px;background:radial-gradient(ellipse at 50% 30%,#2b58c8,var(--space) 45%,var(--navy-deep) 90%)}
.torn{position:absolute;left:0;width:760px}
.audience{position:absolute;left:552px;top:272px;color:var(--white);line-height:1}
.audience .light{font-size:19px;font-weight:400;display:block}
.audience .bold{font-size:19px;font-weight:700;display:block;margin-top:2px}
.audience .big{font-family:"Bebas Neue",sans-serif;font-size:58px;color:var(--gold);display:block;margin-top:2px;line-height:52px}
.audience .caps{font-size:24px;font-weight:800;display:block;line-height:24px}
.book-stage{position:absolute;left:31px;top:265px;width:492px;height:275px;background:linear-gradient(90deg,#e1e02a 0 45%,#f2f2f2 45% 100%);border-radius:3px;box-shadow:0 12px 20px rgba(0,0,0,.25)}
.seal{position:absolute;left:576px;top:444px;width:130px;height:130px;border-radius:50%;background:radial-gradient(circle,#2a2a2a 0 52%,var(--gold) 54% 100%);box-shadow:0 6px 12px rgba(0,0,0,.2)}
.features{position:absolute;left:0;top:600px;width:760px;height:240px}
.feature{position:absolute;top:0;width:170px;text-align:center}
.feature-icon{display:block;margin:0 auto;width:76px;height:76px}
.feature-title{font-family:"Bebas Neue",sans-serif;font-weight:400;font-size:22px;line-height:24px;margin-top:10px;white-space:nowrap}
.feature-body{font-size:13px;line-height:15px;margin:4px auto 0;width:156px}
.divider{position:absolute;top:0;width:1px;height:225px;background:linear-gradient(var(--rule),var(--rule) 70%,transparent)}
.contents{position:absolute;left:0;top:848px;width:760px;height:352px;background:var(--navy)}
.contents-title{position:absolute;left:0;top:30px;width:760px;display:flex;justify-content:center;align-items:center;gap:8px;color:var(--white);font-weight:700;font-size:22px}
.contents-title::before,.contents-title::after{content:"";width:80px;height:1px;background:rgba(255,255,255,.7)}
.chapter-list{position:absolute;list-style:none;color:var(--white);font-size:14.5px;line-height:16.5px}
.chapter-list li{position:absolute;left:0;width:180px;padding-left:26px}
.chapter-list svg{position:absolute;left:0;top:1px;width:15px;height:15px}
.list-left{left:58px;top:100px}
.list-right{left:505px;top:100px}
.list-right li{width:210px}
.book-small{position:absolute;left:248px;top:101px;width:206px;height:196px;background:linear-gradient(90deg,#d8d72a 0 35%,#e7e626 35%);border-radius:2px;box-shadow:0 10px 18px rgba(0,0,0,.35)}
</style>
</head>
<body>
<main class="poster">
  <section class="hero-top">
    <h1 class="headline headline-main">EMBARK ON A MIND</h1>
    <p class="headline headline-sub">BENDING JOURNEY INTO THE REALM OF</p>
    <p class="headline headline-topic">QUANTUM PHYSICS</p>
  </section>

  <section class="space-band" role="img" aria-label="Starry deep-space background with a glowing planet horizon"></section>
  <svg class="torn" style="top:206px" width="760" height="40" viewBox="0 0 760 40" aria-hidden="true">
    <path d="M0 14 L20 8 L38 16 L60 6 L84 14 L110 7 L130 15 L160 9 L186 17 L210 8 L240 13 L270 6 L300 15 L330 9 L356 16 L390 8 L420 14 L450 7 L480 16 L510 9 L540 14 L570 6 L600 15 L630 10 L660 17 L690 8 L720 14 L760 7 L760 40 L740 30 L710 36 L680 28 L650 35 L620 27 L590 34 L560 29 L530 36 L500 27 L470 33 L440 28 L410 36 L380 29 L350 34 L320 27 L290 35 L260 29 L230 36 L200 28 L170 34 L140 27 L110 35 L80 29 L50 36 L20 28 L0 33 Z" fill="#ffffff"/>
    <path d="M0 33 L20 28 L50 36 L80 29 L110 35 L140 27 L170 34 L200 28 L230 36 L260 29 L290 35 L320 27 L350 34 L380 29 L410 36 L440 28 L470 33 L500 27 L530 36 L560 29 L590 34 L620 27 L650 35 L680 28 L710 36 L740 30 L760 40 L0 40 Z" fill="#0d2a7a"/>
  </svg>
  <svg class="torn" style="top:425px" width="760" height="30" viewBox="0 0 760 30" aria-hidden="true">
    <path d="M0 0 L760 0 L760 12 L730 20 L700 10 L670 18 L640 8 L610 16 L580 9 L560 15 L0 15 Z" fill="#0b1642"/>
    <path d="M0 15 L560 15 L580 9 L610 16 L640 8 L670 18 L700 10 L730 20 L760 12 L760 30 L0 30 Z" fill="#ffffff"/>
  </svg>

  <div class="book-stage" role="img" aria-label="Yellow paperback book mockup standing beside an open copy showing its table of contents"></div>

  <p class="audience">
    <span class="light">Ideal for</span>
    <span class="bold">science students</span>
    <span class="big">QUANTUM</span>
    <span class="caps">COMPUTING</span>
    <span class="caps">ENTHUSIASTS</span>
  </p>

  <div class="seal" role="img" aria-label="Gold starburst seal reading: Perfect gift for the Science Lover"></div>

  <section class="features">
    <article class="feature" style="left:31px">
      <svg class="feature-icon" viewBox="0 0 76 76" role="img" aria-label="Icon: atom on a monitor"><circle cx="38" cy="38" r="36" fill="#222" stroke="#fff" stroke-width="2"/><circle cx="38" cy="38" r="37" fill="none" stroke="#222" stroke-width="1"/></svg>
      <h2 class="feature-title">HISTORY OF<br>QUANTUM MECHANICS</h2>
      <p class="feature-body">Explore the fascinating history of quantum mechanics and the brilliant minds behind its development</p>
    </article>
    <div class="divider" style="left:200px"></div>
    <article class="feature" style="left:213px">
      <svg class="feature-icon" viewBox="0 0 76 76" role="img" aria-label="Icon: balance scales over a book"><circle cx="38" cy="38" r="36" fill="#f6ee1a" stroke="#222" stroke-width="2"/></svg>
      <h2 class="feature-title">FUNDAMENTAL PRINCIPLES<br>OF WAVE-PARTICLE</h2>
      <p class="feature-body">Grasp the fundamental principles ofwave-particle duality, quantum states, and the uncertainty principle</p>
    </article>
    <div class="divider" style="left:393px"></div>
    <article class="feature" style="left:388px">
      <svg class="feature-icon" viewBox="0 0 76 76" role="img" aria-label="Icon: atom"><circle cx="38" cy="38" r="36" fill="#222" stroke="#fff" stroke-width="2"/><circle cx="38" cy="38" r="37" fill="none" stroke="#222" stroke-width="1"/></svg>
      <h2 class="feature-title">QUANTUM<br>ENTANGLEMENT</h2>
      <p class="feature-body">Dive into the strange and counterintuitive world of quantum entanglement and its implications for reality itself</p>
    </article>
    <div class="divider" style="left:553px"></div>
    <article class="feature" style="left:556px">
      <svg class="feature-icon" viewBox="0 0 76 76" role="img" aria-label="Icon: padlock on a circuit"><circle cx="38" cy="38" r="36" fill="#f6ee1a" stroke="#222" stroke-width="2"/></svg>
      <h2 class="feature-title">QUANTUM COMPUTING<br>TO CRYPTOGRAPHY</h2>
      <p class="feature-body">Learn about the cutting-edge applications of quantum mechanics, from quantum computing to cryptography</p>
    </article>
  </section>

  <section class="contents">
    <h2 class="contents-title">IN THIS BOOK YOU WILL FIND</h2>
    <ul class="chapter-list list-left">
      <li style="top:0"><svg viewBox="0 0 15 15"><circle cx="7.5" cy="7.5" r="7.5" fill="#f2e41a"/><path d="M4 7.8 L6.5 10 L11 5" stroke="#14205a" stroke-width="1.8" fill="none"/></svg>The Quantum World Unveiled</li>
      <li style="top:50px"><svg viewBox="0 0 15 15"><circle cx="7.5" cy="7.5" r="7.5" fill="#f2e41a"/><path d="M4 7.8 L6.5 10 L11 5" stroke="#14205a" stroke-width="1.8" fill="none"/></svg>The Mathematical<br>Symphony of<br>Quantum Mechanics</li>
      <li style="top:117px"><svg viewBox="0 0 15 15"><circle cx="7.5" cy="7.5" r="7.5" fill="#f2e41a"/><path d="M4 7.8 L6.5 10 L11 5" stroke="#14205a" stroke-width="1.8" fill="none"/></svg>Beyond Classical Boundaries</li>
      <li style="top:167px"><svg viewBox="0 0 15 15"><circle cx="7.5" cy="7.5" r="7.5" fill="#f2e41a"/><path d="M4 7.8 L6.5 10 L11 5" stroke="#14205a" stroke-width="1.8" fill="none"/></svg>Quantum Mechanics at Work</li>
    </ul>
    <div class="book-small" role="img" aria-label="Yellow paperback book mockup with its back cover behind"></div>
    <ul class="chapter-list list-right">
      <li style="top:0"><svg viewBox="0 0 15 15"><circle cx="7.5" cy="7.5" r="7.5" fill="#f2e41a"/><path d="M4 7.8 L6.5 10 L11 5" stroke="#14205a" stroke-width="1.8" fill="none"/></svg>Bridging Quantum Mechanics and Relativity</li>
      <li style="top:50px"><svg viewBox="0 0 15 15"><circle cx="7.5" cy="7.5" r="7.5" fill="#f2e41a"/><path d="M4 7.8 L6.5 10 L11 5" stroke="#14205a" stroke-width="1.8" fill="none"/></svg>Quantum Paradoxes and Thought Experiments</li>
      <li style="top:100px"><svg viewBox="0 0 15 15"><circle cx="7.5" cy="7.5" r="7.5" fill="#f2e41a"/><path d="M4 7.8 L6.5 10 L11 5" stroke="#14205a" stroke-width="1.8" fill="none"/></svg>Quantum Mechanics for the Curious Mind</li>
      <li style="top:150px"><svg viewBox="0 0 15 15"><circle cx="7.5" cy="7.5" r="7.5" fill="#f2e41a"/><path d="M4 7.8 L6.5 10 L11 5" stroke="#14205a" stroke-width="1.8" fill="none"/></svg>Quantum Mechanics Demystified - A Practical Guide</li>
    </ul>
  </section>
</main>
</body>
</html>
```